Request for Business Card Design

Hi. My name is Marlene, I am looking for a new business card design for my company, Quarrow Signal Instruments, LLC. I really like the design you did for Tarsel Venture and was hoping you could do something similar using our full logo and our mark. I am also open to any raised texture design using our mark. I have attached our full logo, which would need to be somewhere on the card, as well as the mark in both outline and full form, as well as our brand colors / guide. The card does not have to be white, as long as our logo and mark appear. I actually like darker colored business cards more, but am open to all options. If you are interested in working with me, please let me know. We would also take the business card design into letterhead design if you can do that.

```html
<!DOCTYPE html>
<html lang="en">
<head>
<meta charset="utf-8">
<title>Quarrow Signal Instruments – Business Card</title>
<link href="https://fonts.googleapis.com/css2?family=Barlow:wght@600&family=Montserrat:wght@400;700&display=swap" rel="stylesheet">
<style>
  :root {
    --backdrop: #2e2825;
    --card: #1c1c1e;
    --brand-blue: #0a9cc8;
    --ink-light: #ffffff;
    --ink-soft: #d9d9d9;
  }
  html, body {
    margin: 0;
    width: 1200px;
    height: 786px;
    overflow: hidden;
    background: var(--backdrop);
  }
  .stage {
    position: relative;
    width: 1200px;
    height: 786px;
  }
  .card {
    position: absolute;
    top: 243px;
    width: 520px;
    height: 300px;
    background: var(--card);
    overflow: hidden;
    box-shadow: 0 10px 30px rgba(0,0,0,.45);
  }
  .card--front { left: 60px; }
  .card--back { left: 620px; }

  .brand {
    position: absolute;
    display: flex;
    align-items: center;
    gap: 16px;
  }
  .brand__dot {
    flex: none;
    border-radius: 50%;
    background: var(--brand-blue);
  }
  .brand__name {
    font-family: "Barlow", sans-serif;
    font-weight: 600;
    color: var(--ink-light);
    text-transform: uppercase;
    line-height: 1;
  }
  .brand__name span { display: block; }
  .brand__main { font-size: 44px; letter-spacing: 4px; }
  .brand__sub { font-size: 12.5px; letter-spacing: 1.2px; margin-top: 4px; }

  .card--front .brand { left: 40px; top: 60px; }
  .card--front .brand__dot { width: 58px; height: 58px; }

  .person {
    position: absolute;
    left: 40px;
    top: 168px;
    width: 170px;
    text-align: right;
    font-family: "Montserrat", sans-serif;
  }
  .person__name {
    font-weight: 700;
    font-size: 21px;
    color: var(--brand-blue);
  }
  .person__role {
    font-size: 11px;
    color: var(--ink-soft);
    margin-top: 2px;
  }
  .divider {
    position: absolute;
    left: 232px;
    top: 160px;
    width: 2px;
    height: 50px;
    background: var(--brand-blue);
  }
  .contact {
    position: absolute;
    left: 250px;
    top: 156px;
    margin: 0;
    padding: 0;
    list-style: none;
    font-family: "Montserrat", sans-serif;
    font-size: 11px;
    color: var(--ink-light);
  }
  .contact li {
    display: flex;
    align-items: center;
    gap: 7px;
    height: 18px;
  }
  .contact svg { width: 10px; height: 10px; fill: var(--brand-blue); }

  .band { position: absolute; left: 0; top: 0; }
  .address {
    position: absolute;
    left: 40px;
    top: 272px;
    font-family: "Montserrat", sans-serif;
    font-size: 12px;
    color: var(--ink-light);
  }

  .card--back .brand { left: 110px; top: 104px; }
  .card--back .brand__dot { width: 62px; height: 62px; }
  .card--back .brand__main { font-size: 42px; }
  .back-stripe {
    position: absolute;
    left: 0;
    right: 0;
    top: 252px;
    height: 6px;
    background: var(--brand-blue);
  }
</style>
</head>
<body>
<main class="stage">
  <section class="card card--front">
    <svg class="band" width="520" height="300" viewBox="0 0 520 300" aria-hidden="true">
      <polygon points="0,262 330,262 420,214 520,214 520,300 0,300" fill="var(--brand-blue)"/>
      <circle cx="478" cy="238" r="15" fill="var(--card)"/>
    </svg>

    <div class="brand">
      <div class="brand__dot"></div>
      <div class="brand__name">
        <span class="brand__main">Quarrow</span>
        <span class="brand__sub">Signal Instruments</span>
      </div>
    </div>

    <div class="person">
      <div class="person__name">Dorian Hale</div>
      <div class="person__role">Owner</div>
    </div>

    <div class="divider"></div>

    <ul class="contact">
      <li>
        <svg viewBox="0 0 10 10" aria-hidden="true"><path d="M2 0.5 L4 2.5 L3 3.8 Q4.5 6 6.2 7 L7.5 6 L9.5 8 L8 9.5 Q3 9 0.5 2 Z"/></svg>
        +001 303 555 0142
      </li>
      <li>
        <svg viewBox="0 0 10 10" aria-hidden="true"><path d="M0 2 H10 V8 H0 Z M0.8 2.6 L5 5.6 L9.2 2.6" stroke="var(--card)" stroke-width="0.8"/></svg>
        info@quarrowsignal.com
      </li>
      <li>
        <svg viewBox="0 0 10 10" aria-hidden="true"><circle cx="5" cy="5" r="4.6"/><path d="M0.6 5 H9.4 M5 0.4 V9.6" stroke="var(--card)" stroke-width="0.7"/></svg>
        www.quarrowsignal.com
      </li>
    </ul>

    <div class="address">1180 Harbor Field Road, Alder Creek, CO 80417</div>
  </section>

  <section class="card card--back">
    <div class="brand">
      <div class="brand__dot"></div>
      <div class="brand__name">
        <span class="brand__main">Quarrow</span>
        <span class="brand__sub">Signal Instruments</span>
      </div>
    </div>
    <div class="back-stripe"></div>
  </section>
</main>
</body>
</html>
```